Web Design Project - Old Dellmoor (Bar)

We need a website for a new wine bar/hotel opening in Sydney's Kings Cross area. The concept is a rustic Australiana bar. We intend to use raw materials (sandstone, rusty metal etc) and lots of greenery/plants. It is set to be stylish and accessible to a young and middle age clientele.

The idea is to bring the outside inside.

The venue can cater for 450 people and is in one of the major nightclub strips in Australia. The demographic differs from celebrities to backpackers.
Updates

Target Market(s)

We are targeting 23yr - 40yr olds.

Industry/Entity Type

Hotel

Requirements
Must have
• What I want is a design to reflect is the fit out of the bar. We would like to see a rustic design to reflect the theme of the bar. The theme behind the fit out will be "bringing the outside inside" with lots of plants, wet walls etc.. There will be exposed brickwork, sandstone, timber and rusted steel with laser cut designs throughout the venue.
Nice to have
• I've attached some 3D designs that the venue will be roughly based on.

```html
<!DOCTYPE html>
<html lang="en">
<head>
<meta charset="utf-8">
<title>Old Dellmoor – Menu</title>
<link rel="stylesheet" href="https://fonts.googleapis.com/css2?family=Alegreya:wght@400;700;800&family=Cinzel:wght@400&family=Open+Sans:wght@400;600;700&display=swap">
<style>
  :root {
    --wood-dark: #2a1c12;
    --wood-mid: #4a3626;
    --header-tan: #8a6c50;
    --header-light: #a88a6c;
    --nav-brown: #361404;
    --nav-text: #e5bf85;
    --nav-active: #f6e6c8;
    --page-tan: #ddb987;
    --title-red: #6e0c0c;
    --ink: #2b1608;
    --card-cream: #f2ddb6;
    --button-tan: #d5b07c;
    --accent-red: #a4150f;
    --dot-line: #d8b68a;
    --leather-1: #a77b40;
    --leather-2: #c9a264;
    --star-red: #7c1210;
  }
  * { box-sizing: border-box; margin: 0; padding: 0; }
  html, body { width: 904px; height: 1200px; overflow: hidden; background: var(--wood-dark); }
  .site { position: relative; width: 904px; height: 1200px; font-family: "Alegreya", Georgia, serif; color: var(--ink); }

  .wood-strip { position: absolute; left: 0; width: 904px;
    background: repeating-linear-gradient(90deg, var(--wood-mid) 0 52px, #3a2a1e 52px 54px, #56412f 54px 104px, #2f2218 104px 106px); }
  .wood-strip.top { top: 0; height: 69px; }
  .wood-strip.bottom { top: 1178px; height: 22px; }
  .rule-dark { position: absolute; top: 69px; left: 0; width: 904px; height: 9px; background: #3a1606; }

  .masthead { position: absolute; top: 78px; left: 0; width: 904px; height: 187px;
    background: linear-gradient(180deg, var(--header-light) 0%, var(--header-tan) 60%, #6e5440 100%); }
  .masthead .star { position: absolute; top: 72px; width: 36px; height: 36px; }
  .masthead .star.left { left: 106px; }
  .masthead .star.right { left: 762px; }
  .brand { position: absolute; top: 0; left: 0; width: 904px; height: 187px; display: flex; flex-direction: column; align-items: center; justify-content: center; gap: 14px; }
  .brand-mark { width: 54px; height: 54px; background: #111; }
  .brand-name { font-family: "Cinzel", Georgia, serif; font-size: 28px; color: #111; letter-spacing: 1px; }

  .main-nav { position: absolute; top: 265px; left: 0; width: 904px; height: 52px; background: var(--nav-brown);
    border-top: 1px dashed var(--dot-line); border-bottom: 1px dashed var(--dot-line); }
  .main-nav ul { list-style: none; display: flex; height: 100%; align-items: center; }
  .main-nav li { font-family: "Open Sans", Arial, sans-serif; font-weight: 700; font-size: 16px; color: var(--nav-text); text-align: center; }
  .main-nav li.active { color: var(--nav-active); }

  .menu-section { position: absolute; top: 317px; left: 0; width: 904px; height: 580px; background: var(--page-tan); }
  .menu-section h1 { position: absolute; left: 36px; top: 34px; font-size: 50px; font-weight: 800; color: var(--title-red); line-height: 1; }
  .menu-section .lede { position: absolute; left: 36px; top: 92px; font-size: 21px; color: var(--ink); }
  .category { position: absolute; width: 404px; }
  .category .photo { width: 404px; height: 173px; border: 2px solid #f0dcbc; border-radius: 3px; }
  .category .label { text-align: center; font-size: 18px; margin-top: 8px; }

  .info-band { position: absolute; top: 897px; left: 0; width: 904px; height: 225px; background: var(--nav-brown);
    border-top: 1px dashed var(--dot-line); border-bottom: 1px dashed var(--dot-line); }
  .info-card { position: absolute; top: 35px; width: 261px; height: 147px; background: var(--card-cream); border-radius: 2px; text-align: center; padding-top: 28px; }
  .info-card h2 { font-size: 27px; font-weight: 700; text-transform: uppercase; line-height: 1; color: var(--ink); }
  .info-card p { font-family: "Open Sans", Arial, sans-serif; font-size: 13px; color: #3a2a1c; margin-top: 6px; line-height: 1.35; }
  .info-card .cta { display: block; margin: 8px auto 0; width: 221px; height: 36px; background: var(--button-tan); border-radius: 3px;
    font-size: 17px; font-weight: 700; color: var(--accent-red); line-height: 36px; text-transform: uppercase; }
  .info-card .hours { font-size: 21px; font-weight: 700; color: var(--accent-red); margin-top: 12px; }

  .site-footer { position: absolute; top: 1122px; left: 0; width: 904px; height: 56px;
    background: linear-gradient(180deg, var(--leather-1), var(--leather-2) 50%, var(--leather-1)); }
  .site-footer .copy { position: absolute; left: 29px; top: 19px; font-family: "Open Sans", Arial, sans-serif; font-size: 13px; color: #fff; }
  .social { position: absolute; right: 22px; top: 19px; display: flex; gap: 12px; }
  .social span { width: 16px; height: 16px; border-radius: 50%; background: #fff; }
</style>
</head>
<body>
<div class="site">
  <div class="wood-strip top"></div>
  <div class="rule-dark"></div>

  <header class="masthead">
    <svg class="star left" viewBox="0 0 24 24"><polygon fill="var(--star-red)" points="12,1 15,9 23,9 16.5,14 19,22 12,17 5,22 7.5,14 1,9 9,9"/></svg>
    <svg class="star right" viewBox="0 0 24 24"><polygon fill="var(--star-red)" points="12,1 15,9 23,9 16.5,14 19,22 12,17 5,22 7.5,14 1,9 9,9"/></svg>
    <div class="brand">
      <div class="brand-mark"></div>
      <div class="brand-name">OLD DELLMOOR</div>
    </div>
  </header>

  <nav class="main-nav">
    <ul>
      <li style="width:196px">HOME</li>
      <li style="width:164px">ABOUT US</li>
      <li style="width:220px" class="active">MENU</li>
      <li style="width:176px">RESERVATIONS</li>
      <li style="width:148px">LOCATION</li>
    </ul>
  </nav>

  <main class="menu-section">
    <h1>Menu</h1>
    <p class="lede">What's on your menu? Click to edit me</p>

    <div class="category" style="left:32px; top:133px;">
      <div class="photo" role="img" aria-label="Photo of baked potatoes with a pewter plate and gravy boat" style="background:linear-gradient(120deg,#3a2412,#8a6a44 55%,#d9c08a)"></div>
      <div class="label">Appetizers</div>
    </div>
    <div class="category" style="left:466px; top:133px;">
      <div class="photo" role="img" aria-label="Photo of a green salad with pear and soft cheese" style="background:linear-gradient(120deg,#5f8a38,#c68a3a 50%,#6c2a2a)"></div>
      <div class="label">Soup, Salads &amp; Sides</div>
    </div>
    <div class="category" style="left:32px; top:354px;">
      <div class="photo" role="img" aria-label="Photo of a grilled steak with roast potatoes and rosemary" style="background:linear-gradient(100deg,#d7a54a,#7a4a2a 55%,#4a2a1a)"></div>
      <div class="label">Entrees</div>
    </div>
    <div class="category" style="left:466px; top:354px;">
      <div class="photo" role="img" aria-label="Photo of stacked chocolate brownies" style="background:linear-gradient(100deg,#cfd0d4,#5a3020 50%,#3e2014)"></div>
      <div class="label">Desserts</div>
    </div>
  </main>

  <section class="info-band">
    <div class="info-card" style="left:33px;">
      <h2>Where are we?</h2>
      <p>418 Ferncliff Rd. Sydney, AU 20110</p>
      <span class="cta">Get directions now</span>
    </div>
    <div class="info-card" style="left:320px;">
      <h2>Opening hours</h2>
      <p>We're open everyday</p>
      <div class="hours">12:00pm-1:00am</div>
    </div>
    <div class="info-card" style="left:609px; padding-top:26px;">
      <h2>Chef at home</h2>
      <p>I'm a Paragraph. Click here to add<br>your own text and edit me. It's easy.<br>Just click “Edit Text”</p>
    </div>
  </section>

  <footer class="site-footer">
    <div class="copy">© 2013 by Old Dellmoor.</div>
    <div class="social"><span></span><span></span><span></span></div>
  </footer>

  <div class="wood-strip bottom"></div>
</div>
</body>
</html>
```